Quill Harbor (IT/Network Services)

Quill Harbor, LLC provides technology services to small and medium businesses. Essentially, anytime you've every thought your business might need an "IT guy" to handle something you could instead call us to handle it. Basically, you can outsource your IT needs to us.

This is a brand new company and so we'll need a brand new website. I'd like to use WordPress to handle the site since that will make things easier for me to maintain in the long run.

The site should include a, more-or-less, static front page with the dynamic data occurring on pages linked from a navigational area.

I have a logo already designed that I would like to see used in the design. The one with "white" in the title is the official logo, just added some other versions for your perusal.

Color queues from the logo but feel free to add other colors where applicable.

The site should feel somewhat corporate but with a "younger" slant (something a 25-35 year old would enjoy).

Pages (either to be added initially or by me after design completion):
"About" section - includes company history, business philosophy, etc.
"Services" section - service options, service approach, service specifics
"Testimonials" section - (eventually)
"News" section - (eventually) industry news, company news, events, blog
Contact Links

Websites to view:
The two largest local competitors:
http://www.brightmarsh-tech.example/
http://www.kelvarworks.example/
Other local competitors:
http://www.tpbllc.example/
http://www.morrowfield.example/

Other info you might find useful:
Domain: qhllc.example
Address:
417 Elm Row S
Suite 512B
Nashville, TN 37288
Phone: 615-555-0187
Emails available for use/display:
info@qhllc.example
sales@qhllc.example

Target Market(s)

Our target clients are mainly small businesses (25 or less computer users) which means we're looking at a lot of start-ups or younger companies. We'll be interacting with many entrepreneurs and young business owners.

Requirements
Must have
• Need full WP theme (not a mockup)

```html
<!DOCTYPE html>
<html lang="en">
<head>
<meta charset="utf-8">
<title>Quill Harbor, LLC</title>
<link href="https://fonts.googleapis.com/css2?family=Source+Sans+3:ital,wght@0,400;0,600;1,400&display=swap" rel="stylesheet">
<style>
:root{
  --orange:#f08c00;
  --orange-light:#f7a21b;
  --orange-dark:#d97a00;
  --text:#6b6b6b;
  --text-dark:#3f3f3f;
  --blue-deep:#0b6fb0;
  --blue-mid:#58b6ee;
  --blue-pale:#bfe4fb;
  --card:#f3f3f3;
  --line:#d9d9d9;
  --white:#ffffff;
  --page:#e6e6e6;
  --social:#8fb4dc;
}
*{box-sizing:border-box;margin:0;padding:0}
html,body{width:939px;height:1200px;overflow:hidden}
body{background:var(--page);font-family:"Source Sans 3",Arial,sans-serif;color:var(--text)}
.page{position:relative;width:939px;height:1200px;background:var(--white);overflow:hidden}
.abs{position:absolute}

.utility{left:637px;top:12px;width:282px;height:31px;background:#ececec;border-radius:0 0 0 6px;font-size:12px;color:#555;display:flex;align-items:center;justify-content:center;gap:12px}
.utility .sep{color:#999}

.brand{left:23px;top:70px;display:flex;align-items:center;gap:10px}
.brand .dot{width:34px;height:34px;border-radius:50%;background:var(--orange)}
.brand .name{font-size:30px;font-weight:600;color:var(--orange);letter-spacing:.5px}

.touch{left:762px;top:74px;display:flex;align-items:center;gap:6px;font-size:14px;color:#555}
.touch .soc{width:29px;height:29px;border-radius:50%;background:var(--social);border:2px solid #e4e4e4}
.touch .soc:first-of-type{margin-left:4px}

.search{left:655px;top:117px;width:260px;height:24px;border:1px solid #d3d3d3;border-radius:4px;background:#fff;box-shadow:inset 0 1px 2px rgba(0,0,0,.12)}
.search span{position:absolute;left:8px;top:4px;font-size:11px;font-style:italic;color:#aaa}
.search .go{position:absolute;right:-2px;top:-2px;width:28px;height:28px;border-radius:50%;background:var(--orange);color:#fff;font-size:11px;font-weight:600;display:flex;align-items:center;justify-content:center}

.nav{left:7px;top:167px;width:921px;height:45px;background:linear-gradient(var(--orange-light),var(--orange));border-radius:4px;display:flex}
.nav a{color:#fff;text-decoration:none;font-size:14px;font-weight:600;display:flex;align-items:center;justify-content:center;border-right:1px solid var(--orange-dark)}
.nav a:last-child{border-right:none}

.hero{left:9px;top:218px;width:920px;height:307px;background:linear-gradient(100deg,var(--blue-pale) 0%,var(--blue-mid) 45%,#7cc8f4 70%,var(--blue-pale) 100%)}
.hero-visual{left:518px;top:237px;width:305px;height:272px;border-radius:6px;background:linear-gradient(160deg,#4fb0e8 0%,#2f8fd0 55%,#a9d8f5 100%);opacity:.85}
.punch{left:128px;top:316px;width:390px;height:124px;background:rgba(255,255,255,.96);padding:12px 0 0 24px}
.punch h2{font-size:24px;font-weight:400;color:var(--orange);line-height:1.1;margin-bottom:6px}
.punch p{font-size:10.5px;line-height:15.5px;color:var(--blue-deep);width:355px}
.punch .pager{display:flex;gap:3px;margin-top:8px}
.punch .pager i{width:8px;height:7px;background:#222;display:block}

.welcome{left:22px;top:541px;width:572px}
.welcome h1{font-size:18px;font-weight:400;color:var(--orange);margin-bottom:9px}
.welcome p{font-size:10.5px;line-height:15.6px;color:var(--text)}
.welcome p+p{margin-top:15.6px}
.dotted{left:23px;top:747px;width:584px;border-top:2px dotted #b5b5b5}

.testi-title{left:23px;top:763px;font-size:18px;color:var(--orange)}
.card{width:292px;height:127px;background:var(--card);border-radius:5px;padding:13px 20px 0 12px}
.card p{font-size:10px;line-height:15.6px;font-style:italic;color:#555}
.card p em{font-size:12.5px;color:#444}
.card .by{text-align:right;font-size:13px;color:#444;margin-top:3px;padding-right:0}
.rule{left:23px;top:1080px;width:590px;border-top:1px solid var(--line)}
.view-all{left:549px;top:1089px;font-size:13px;font-weight:600;color:var(--orange)}

.divider-v{left:639px;top:537px;height:548px;border-left:1px solid var(--line)}
.news-title{left:653px;top:537px;font-size:17px;color:var(--text-dark)}
.news{left:654px;width:256px}
.news .date{font-size:12px;color:#333;margin-bottom:10px}
.news h3{font-size:12.5px;font-weight:400;line-height:15.6px;color:#666;margin-bottom:10px;padding-right:8px}
.news p{font-size:10.5px;line-height:15.6px;color:var(--text);padding-right:4px}
.news .more{text-align:right;font-size:12px;color:var(--orange);margin-top:8px}
.news-rule{left:639px;width:272px;border-top:1px solid var(--line)}

.footer{left:0;top:1111px;width:939px;height:89px;background:var(--orange)}
.footer .links{position:absolute;left:10px;top:20px;font-size:10.5px;color:#fff;display:flex;gap:10px}
.footer .copy{position:absolute;left:11px;top:44px;font-size:10px;color:#fff}
.footer .connect{position:absolute;left:755px;top:20px;display:flex;align-items:center;gap:8px;color:#fff;font-size:11px}
.footer .soc{width:31px;height:31px;border-radius:50%;background:#fff;opacity:.92}
.footer .soc:first-of-type{margin-left:6px}
</style>
</head>
<body>
<div class="page">

  <div class="abs utility"><span>Member Login</span><span class="sep">|</span><span>Sitemap</span><span class="sep">|</span><span>Request Quote</span></div>

  <div class="abs brand"><span class="dot"></span><span class="name">Quill Harbor</span></div>

  <div class="abs touch">Get In Touch <span class="soc" role="img" aria-label="Social link"></span><span class="soc" role="img" aria-label="Social link"></span></div>

  <div class="abs search"><span>type your word here..</span><div class="go">Go</div></div>

  <nav class="abs nav">
    <a style="width:121px">Home</a>
    <a style="width:173px">About Company</a>
    <a style="width:122px">Services</a>
    <a style="width:146px">Testimonials</a>
    <a style="width:91px">News</a>
    <a style="width:110px">Partner</a>
    <a style="width:158px">Contact Us</a>
  </nav>

  <div class="abs hero" role="img" aria-label="Blue technology themed banner with streams of digits"></div>
  <div class="abs hero-visual" role="img" aria-label="Product photo of a desktop computer with a blue technology scene on screen"></div>

  <div class="abs punch">
    <h2>Punch Line goes here</h2>
    <p>At Lumenvale esolutions we use all the latest technologies for web designing. Lumenvale esolutions provides the best web designing which compels the customers to ask and inquire about.</p>
    <div class="pager"><i></i><i></i><i></i><i></i></div>
  </div>

  <section class="abs welcome">
    <h1>Welcome to Quill Harbor Website Mainpage</h1>
    <p>E-Commerce is a major progress in technology that has changed the way in which the customers now purchase information, products and the services. It's the new way of providing an opportunity to make your products and services available in the global market 24 hours a day through Internet<br>Lumenvale eSolutions is specialized in handling advanced web projects and the ongoing projects that require permanent maintenance and support .We like challenges and do complete these challenge with expertise we like solving questions that arises in such projects as these helps us to grow also.</p>
    <p>When consiering advanced web development project, finding the right answers to the hard questions is a challenge for any firm, it includes expertise and enables Lumenvale eSolutions to specialize in advanced projects and ongoing projects that require permanent support and maintenance.</p>
  </section>
  <div class="abs dotted"></div>

  <h2 class="abs testi-title" style="font-weight:400">Testimonials</h2>
  <div class="abs card" style="left:22px;top:794px"><p><em>Static website are the which are usually been used and are benefited through</em> the Professionals and Small Companies. The companies with fewer budgets can promote their products and services through the static website and gain a lot.</p><div class="by">BY AUTHOR NAME</div></div>
  <div class="abs card" style="left:321px;top:796px"><p><em>Static website are the which are usually been used and are benefited through</em> the Professionals and Small Companies. The companies with fewer budgets can promote their products and services through the static website and gain a lot.</p><div class="by">BY AUTHOR NAME</div></div>
  <div class="abs card" style="left:20px;top:936px;padding-left:21px;padding-right:14px"><p><em>Static website are the which are usually been used and are benefited through</em> the Professionals and Small Companies. The companies with fewer budgets can promote their products and services through the static website and gain a lot.</p><div class="by">BY AUTHOR NAME</div></div>
  <div class="abs card" style="left:321px;top:936px"><p><em>Static website are the which are usually been used and are benefited through</em> the Professionals and Small Companies. The companies with fewer budgets can promote their products and services through the static website and gain a lot.</p><div class="by">BY AUTHOR NAME</div></div>
  <div class="abs rule"></div>
  <div class="abs view-all">VIEW ALL</div>

  <div class="abs divider-v"></div>
  <h2 class="abs news-title" style="font-weight:400">Latest News</h2>

  <article class="abs news" style="top:574px">
    <div class="date">20.March.2012</div>
    <h3>E-Commerce is a major progress in technology that has changed the way</h3>
    <p>Which the customers now purchase information, products and the services. It's the new way of providing an opportunity to make your products</p>
    <div class="more">READ MORE</div>
  </article>
  <div class="abs news-rule" style="top:715px"></div>

  <article class="abs news" style="top:730px;left:658px">
    <div class="date">20.March.2012</div>
    <h3>E-Commerce is a major progress in technology that has changed the way</h3>
    <p>Which the customers now purchase information, products and the services. It's the new way of providing an opportunity to make your products</p>
    <div class="more">READ MORE</div>
  </article>
  <div class="abs news-rule" style="top:871px"></div>

  <article class="abs news" style="top:886px;left:658px">
    <div class="date">20.March.2012</div>
    <h3>The simple website are also said as the static web as its embedded on a page.</h3>
    <div class="more">READ MORE</div>
  </article>
  <div class="abs news-rule" style="top:967px"></div>

  <article class="abs news" style="top:990px;left:659px">
    <div class="date">20.March.2012</div>
    <h3 style="margin-bottom:2px">At Lumenvale esolutions we use all the latest technologies for web designing</h3>
    <p>Lumenvale esolutions provides the best web designing which compels the customers to ask</p>
    <div class="more">READ MORE</div>
  </article>

  <footer class="abs footer">
    <div class="links"><span>Home</span><span>|</span><span>About Company</span><span>|</span><span>Services</span><span>|</span><span>Testimonials</span><span>|</span><span>News</span><span>|</span><span>Partner</span><span>|</span><span>Contact Us</span></div>
    <div class="copy">© 2012 Quill Harbor, LLC | All right reserved</div>
    <div class="connect">Get Connect With <span class="soc" role="img" aria-label="Social link"></span><span class="soc" role="img" aria-label="Social link"></span></div>
  </footer>

</div>
</body>
</html>
```